Business cards to launch an education platform

Hi,
I am looking at having new business cards designed.
I am a startup, developing a web platform for schools and university, the education world. It's an online assessment system.
I would like a card that looks classy, and that is using the colors and the font of my logo.

I have attached:
1) my logo
2) A business card that I have designed quickly so you can have all the information required in the card, but I really don't like it.
3) The font that I am using (Lato Regular) to design my web platform
4) Some screenshots of my web platform so you can have a look at the style that I have.

Target Market(s)

Major market: Education system: Schools and university
Minor markets: Business in general

Industry/Entity Type

Business

Contact Information for Business Card

Clara Fenwick
Director

M: 0437 518 902
E: clara.fenwick@amberLoomSystems.com.au

Requirements
Must have
• The colors of my logo

```html
<!DOCTYPE html>
<html lang="en">
<head>
<meta charset="utf-8">
<title>Amber Loom Systems – Business Card</title>
<link rel="stylesheet" href="https://fonts.googleapis.com/css2?family=Lato:wght@400;700&display=swap">
<style>
  :root {
    --page-bg: #e7e4df;
    --card-white: #fbfbfb;
    --card-black: #161515;
    --panel-light: #98dfee;
    --panel-deep: #5bc2de;
    --accent-bar: #5fc4df;
    --brand-navy: #1f4f98;
    --text-dark: #141414;
    --shadow: rgba(0, 0, 0, 0.22);
  }
  * { box-sizing: border-box; margin: 0; padding: 0; }
  html, body {
    width: 1200px;
    height: 892px;
    overflow: hidden;
    background: var(--page-bg);
    font-family: "Lato", Arial, sans-serif;
  }
  .sheet {
    width: 1200px;
    height: 892px;
    display: flex;
    align-items: center;
    justify-content: center;
    gap: 40px;
  }
  .card {
    position: relative;
    width: 540px;
    height: 330px;
    border-radius: 4px;
    box-shadow: 0 10px 26px var(--shadow);
    overflow: hidden;
  }
  /* Front */
  .card--front { background: var(--card-white); }
  .contact-panel {
    position: absolute;
    left: 0;
    top: 26px;
    width: 320px;
    height: 252px;
    border-radius: 0 20px 20px 0;
    background: linear-gradient(150deg, var(--panel-light), var(--panel-deep));
    padding: 26px 28px;
    color: var(--text-dark);
  }
  .person-name {
    font-weight: 700;
    font-size: 32px;
    letter-spacing: -0.3px;
    line-height: 1;
  }
  .person-role {
    font-size: 16px;
    margin-top: 6px;
  }
  .contact-list {
    position: absolute;
    left: 28px;
    bottom: 22px;
    list-style: none;
    font-size: 12.5px;
    line-height: 1.6;
  }
  .contact-list li { display: flex; align-items: center; gap: 8px; white-space: nowrap; }
  .contact-icon { width: 12px; height: 12px; flex: none; }
  .front-brand {
    position: absolute;
    left: 350px;
    top: 178px;
    display: flex;
    align-items: flex-start;
    gap: 10px;
  }
  .brand-name {
    font-weight: 400;
    font-size: 20px;
    letter-spacing: 2px;
    color: var(--brand-navy);
    white-space: nowrap;
  }
  .front-brand .brand-name {
    font-size: 18px;
    letter-spacing: 1.5px;
    line-height: 1.25;
  }
  .brand-line { display: block; }
  .brand-square {
    width: 14px;
    height: 14px;
    background: var(--brand-navy);
    flex: none;
  }
  .front-brand .brand-square { margin-top: 4px; }
  .accent-bar {
    position: absolute;
    right: 0;
    bottom: 22px;
    width: 170px;
    height: 26px;
    border-radius: 13px 0 0 13px;
    background: var(--accent-bar);
  }
  /* Back */
  .card--back {
    background: var(--card-black);
    display: flex;
    align-items: center;
    justify-content: center;
  }
  .back-brand {
    display: flex;
    align-items: center;
    gap: 14px;
  }
  .back-brand .brand-name {
    font-size: 30px;
    letter-spacing: 4px;
    color: var(--accent-bar);
  }
  .back-brand .brand-square {
    width: 20px;
    height: 20px;
    background: var(--accent-bar);
  }
</style>
</head>
<body>
<main class="sheet">
  <section class="card card--front" aria-label="Card front">
    <div class="contact-panel">
      <h1 class="person-name">Clara Fenwick</h1>
      <p class="person-role">Director</p>
      <ul class="contact-list">
        <li>
          <svg class="contact-icon" viewBox="0 0 12 12" aria-hidden="true">
            <rect width="12" height="12" rx="2" fill="#141414"/>
            <path d="M3.6 2.6 L5 4.3 L4.3 5 Q5 6.8 7 7.7 L7.7 7 L9.4 8.4 L8.6 9.4 Q4 8.8 2.6 3.4 Z" fill="#8fdcec"/>
          </svg>
          <span>0437 518 902</span>
        </li>
        <li>
          <svg class="contact-icon" viewBox="0 0 12 12" aria-hidden="true">
            <rect width="12" height="12" rx="2" fill="#141414"/>
            <rect x="2.5" y="3.5" width="7" height="5" fill="none" stroke="#8fdcec" stroke-width="1"/>
            <path d="M2.5 3.5 L6 6.3 L9.5 3.5" fill="none" stroke="#8fdcec" stroke-width="1"/>
          </svg>
          <span>clara.fenwick@amberLoomSystems.com.au</span>
        </li>
      </ul>
    </div>
    <div class="front-brand">
      <span class="brand-square" aria-hidden="true"></span>
      <span class="brand-name">
        <span class="brand-line">Amber Loom</span>
        <span class="brand-line">Systems</span>
      </span>
    </div>
    <div class="accent-bar" aria-hidden="true"></div>
  </section>

  <section class="card card--back" aria-label="Card back">
    <div class="back-brand">
      <span class="brand-square" aria-hidden="true"></span>
      <span class="brand-name">Amber Loom Systems</span>
    </div>
  </section>
</main>
</body>
</html>
```